Machinery Harbor Corp - Business Card Design

Need a new modern designed business card that is different and stands out to represent my equipment financing company. Machinery Harbor Corp finances all types of equipment and all types of industries. We like to do equipment financing a different way by putting customers first and want our card to represent that different approach to business. I want a card that some remembers when they receive it so it sticks in their mind and makes that wow impression.

Card should have a black background so the logo stands out. It can be horizontial or vertical or a combination of both.

Front of card information is below that shows the information that would go on my card. That is where I want a different look or design to stand out. The front could be split black/orange colour so the logo could pop on black side and information on orange side with different lettering. Just outside the box thinking on the front of the card. Open to any type of design.

Back of card is below which i I like unless you have a different spin to provide or a different idea that would make the card better as I am open to anything that looks great.

Target Market(s)

Machinery Harbor Corp deals with business owners in all industries.

Industry/Entity Type

Business

Contact Information for Business Card

Colors

Designer to choose colors to be used in the design.

Requirements
Must have
• Modern
• Different
• Stand Out
• Makes an Impression

```html
<!DOCTYPE html>
<html lang="en">
<head>
<meta charset="utf-8">
<title>Machinery Harbor Corp – Business Card</title>
<link href="https://fonts.googleapis.com/css2?family=Lato:wght@400;700&display=swap" rel="stylesheet">
<style>
  :root {
    --backdrop: #3b322d;
    --card: #1e2022;
    --card-edge: #15171a;
    --orange: #f0682a;
    --silver: #b9bcc0;
    --white: #f4f4f4;
    --divider: #6a6d70;
  }
  html, body {
    margin: 0;
    padding: 0;
    width: 1200px;
    height: 780px;
    overflow: hidden;
    background: var(--backdrop);
  }
  .canvas {
    position: relative;
    width: 1200px;
    height: 780px;
    font-family: "Lato", sans-serif;
  }
  .card {
    position: absolute;
    width: 540px;
    height: 309px;
    background: var(--card);
    border: 1px solid var(--card-edge);
    box-shadow: 0 18px 40px rgba(0,0,0,0.45);
    box-sizing: border-box;
  }
  /* Back of card */
  .card-back {
    left: 40px;
    top: 120px;
    display: flex;
    align-items: center;
    justify-content: center;
  }
  .card-back .brand-name {
    color: var(--silver);
    font-size: 26px;
    font-weight: 700;
    letter-spacing: 1px;
  }
  /* Front of card */
  .card-front {
    left: 620px;
    top: 350px;
    display: flex;
    align-items: center;
  }
  .card-front .brand-block {
    width: 300px;
    display: flex;
    align-items: center;
    justify-content: center;
    gap: 12px;
  }
  .brand-mark {
    width: 14px;
    height: 14px;
    background: var(--orange);
    flex: none;
  }
  .card-front .brand-name {
    color: var(--orange);
    font-size: 24px;
    font-weight: 700;
    line-height: 1.15;
    letter-spacing: 0.5px;
  }
  .divider {
    width: 1px;
    height: 150px;
    background: var(--divider);
  }
  .contact-block {
    flex: 1;
    padding-right: 34px;
    text-align: right;
    color: var(--white);
  }
  .person-name {
    font-size: 21px;
    font-weight: 700;
    text-transform: uppercase;
    margin: 0;
  }
  .person-title {
    font-size: 15px;
    text-transform: uppercase;
    margin: 2px 0 26px;
  }
  .contact-line {
    font-size: 14px;
    margin: 0 0 4px;
  }
</style>
</head>
<body>
<main class="canvas">
  <section class="card card-back" aria-label="Business card back">
    <span class="brand-name">Machinery Harbor Corp</span>
  </section>

  <section class="card card-front" aria-label="Business card front">
    <div class="brand-block">
      <span class="brand-mark"></span>
      <span class="brand-name">Machinery Harbor<br>Corp</span>
    </div>
    <div class="divider"></div>
    <div class="contact-block">
      <p class="person-name">Dane Morrow</p>
      <p class="person-title">President</p>
      <p class="contact-line">www.machineryharborcorp.ca</p>
      <p class="contact-line">403.555.0192</p>
      <p class="contact-line">dane@machineryharborcorp.ca</p>
    </div>
  </section>
</main>
</body>
</html>
```